I need a sophisticated and powerful book cover design that combines Japanese minimalism with contemporary appeal. The cover should convey personal transformation through the metaphor of a katana (Japanese sword).
Key Design Elements:
A katana, either partially shown or artistically rendered
Subtle Japanese design elements without being stereotypical
Clean, minimalist aesthetic
Professional font selection that bridges Eastern and Western typography
Color scheme: Deep blacks, steel grays, and possibly a touch of red or gold for accent
Mood/Style:
Professional and sophisticated
Blend of traditional Japanese aesthetics with modern design
Should appeal to personal development and business readers
Must convey strength and transformation
Elegant rather than aggressive
Specific Requirements:
Title: "The Lantern Compass"
Subtitle: "Quiet Methods for Growing Inner Steadiness and Calm Endurance"
Author names: Dorvelan Thaske and Meloda Thaske
Cover dimensions: Standard hardcover book size (6" x 9")
Must work well in both physical and digital thumbnail formats
Should be striking and legible when viewed as a small image online
Design Specifics:
Japanese elements such as brushstroke effects, kanji characters, or wave patterns
The design should reflect the book's core message: personal transformation through Japanese wisdom principles, using the katana as a metaphor for growth and development.

```html
<!DOCTYPE html>
<html lang="en">
<head>
<meta charset="utf-8">
<title>The Lantern Compass — Book Cover</title>
<link rel="stylesheet" href="https://fonts.googleapis.com/css2?family=Cinzel:wght@400;600;700&family=Shojumaru&display=swap">
<style>
  :root {
    --stage: #000000;
    --paper: #fdf5ee;
    --teal: #037b7d;
    --teal-light: #6cc8cf;
    --steel: #3f5659;
    --ink: #0b0b0b;
  }
  * { margin: 0; padding: 0; box-sizing: border-box; }
  html, body {
    width: 1200px;
    height: 1200px;
    overflow: hidden;
    background: var(--stage);
  }
  .cover {
    position: absolute;
    left: 240px;
    top: 60px;
    width: 720px;
    height: 1080px;
    background: var(--paper);
    text-align: center;
  }
  .title { position: absolute; left: 0; right: 0; top: 40px; }
  .title span { display: block; line-height: 1; }
  .title-the {
    font-family: "Cinzel", serif;
    font-weight: 600;
    font-size: 94px;
    color: var(--teal);
    letter-spacing: 2px;
  }
  .title-key {
    margin-top: 10px;
    font-family: "Shojumaru", cursive;
    font-size: 96px;
    color: var(--ink);
    letter-spacing: 1px;
  }
  .title-main {
    margin-top: 6px;
    font-family: "Cinzel", serif;
    font-weight: 600;
    font-size: 116px;
    color: var(--teal);
    letter-spacing: 0;
  }
  .subtitle {
    position: absolute;
    left: 0; right: 0;
    top: 426px;
    font-family: "Cinzel", serif;
    font-weight: 600;
    font-size: 30px;
    line-height: 45px;
    letter-spacing: 1.5px;
  }
  .subtitle .line { display: block; }
  .subtitle .dark { color: var(--ink); }
  .subtitle .accent { color: var(--teal); }
  .artwork {
    position: absolute;
    left: 130px;
    top: 524px;
    width: 462px;
    height: 460px;
  }
  .authors {
    position: absolute;
    left: 0; right: 0;
    top: 1000px;
    font-family: "Cinzel", serif;
    font-weight: 600;
    font-size: 27px;
    letter-spacing: 1.5px;
    color: var(--teal);
  }
</style>
</head>
<body>
  <main class="cover">
    <h1 class="title">
      <span class="title-the">THE</span>
      <span class="title-key">LANTERN</span>
      <span class="title-main">COMPASS</span>
    </h1>

    <p class="subtitle">
      <span class="line dark">Quiet Methods for</span>
      <span class="line"><span class="accent">Growing Inner Steadiness</span> <span class="dark">and</span></span>
      <span class="line accent">Calm Endurance</span>
    </p>

    <svg class="artwork" viewBox="0 0 462 460" role="img" aria-label="Illustration of two crossed katanas with teal blades and dark wrapped hilts, entwined by flowing smoke-like ribbons">
      <defs>
        <radialGradient id="artGlow" cx="55%" cy="55%" r="60%">
          <stop offset="0%" stop-color="#5fb7bd" stop-opacity="0.75"/>
          <stop offset="55%" stop-color="#3f6f73" stop-opacity="0.45"/>
          <stop offset="100%" stop-color="#fdf5ee" stop-opacity="0"/>
        </radialGradient>
      </defs>
      <rect width="462" height="460" fill="url(#artGlow)"/>
    </svg>

    <p class="authors">Dorvelan Thaske and Meloda Thaske</p>
  </main>
</body>
</html>
```